Systems and Technology Consultants - Website

Design & Build a website for a new company which operates in the Systems and Technology space for Transportation, Government and Commercial sectors.

Overall design should be minimalist in nature.
Should also have a feed that provides news and event updates on the main page.
Logo has already been awarded and should be incorporated into the site.

We like the overall layout, functionality and simplicity of the below sites. Submitted designs could be similar to or a combination of the aspects on these sites, or perhaps a whole different concept - we are open to new ideas.
Norvique.com
Teblo.it

Update 1 Dated 27 May 2014

All I am moving away from the Teblo.it website and would like it to be more aligned with Norvique.com not only in layout but in functionality. I will be extending the deadline of this design brief for two weeks to incorporate additional requirements and will add addtional funding to the project.

Apologies for not having more information available to provide but with so many submissions its getting confusing.

Thanks Derek

Please note that the brief has been updated and the deadline has been extended.

Important: We will need two language versions of the website, English and Arabic; the website is hosted on HostPelican

Hello All, Thank you for your submissions. We have narrowed it down to the final 6 designers and I just wanted to take a moment and provide a bit of feedback regarding the concepts that we like and the modifications we are looking for. First, let me mention some of the design functions we like. - At the top of the homepage we really like the "region" or "language" tab so that the website can be viewed in both English and Arabic. - We like the homepage to have clear color variation so that the different sections of the homepage are distinct. Additionally, we like the bottom portion of the homepage to be in red. We feel that draws attention to our contact information. Again, we would like the colors to integrate black, gray-scale, red, etc. - Having a search tab at the top of the home page, or integrated into the main image, so that the site is easy to navigate. - We especially like the main image to have the scrolling tabs at the bottom so it is easy to browse the services offered (Consultancy, Solutions Architecture, Masters Systems Integration, Independent Design Review). - In regards to the services offered tab we really like the idea that a few people presented that have the outside of our logo with an icon in the middle of consultancy, solutions, etc., etc. Secondly, as mentioned in our brief we really enjoy the design of norvique site. Specially, we enjoy the strong iconic images they use, the way the tabs at the top scroll easily, and contact us page that generates an email. Lastly, I've included some photos of the concept we have been working on. What we are trying to demonstrate is how our company offers a range of services that are essentially linked together. We provide individual services that when combined present the full service package. We would like this concept to be integrated into the over concept of our website. Please feel free to ask for clarification of any of the above points or contact us if you have any additional questions. We appreciate all of your hard work and are very excited to see the updated designs. Best, Marta Vennick Quelbrant Senior Program Manager marta.vennick@quelbrant-example.com

Industry/Entity Type

Government

Font styles to use
Serif
Sans Serif

Requirements
Must have
• Must work on/adapt to various/mobile devices (responsive)
Must be simple and straightforward
Colors should be in line/matching with logo
2 language versions: English and Arabic (no Thai)
Services should be the first group/row of items after/below the main image
Note: the website will be hosted by hostpelican
Nice to have
• Submit feedback form
What's New section
The banner at the bottom of the site should not be too large; we would like a narrow one more
It would be nice if the header/top banner (with Home, About, etc. tabs) could stay in place as you scroll down (like Norvique and Chatterloop)
We will likely only use one image with a Company slogan on the Home page rather than a carousel of images to rotate through
Should not have
• This is the existing website: http://www.quelbrant-example.org
We do not like the animation, the way the banner icons/titles bounce
Not simple enough, we don't like the functionality or how pages load so slowly
We do not like the logo centered - it should be at the left
The banner and its tabs should not be towards the right, we would like them to be centered, to go all the way across and to be below the logo

```html
<!DOCTYPE html>
<html lang="en">
<head>
<meta charset="utf-8">
<title>Quelbrant</title>
<link href="https://fonts.googleapis.com/css2?family=Open+Sans:wght@400;700&family=Roboto:wght@400;500;700&display=swap" rel="stylesheet">
<style>
:root{
  --red:#e8303a;
  --red-dark:#c91f28;
  --blue:#3a87c8;
  --ink:#222;
  --body:#555;
  --grey-row:#dcdcdc;
  --grey-line:#f2f2f2;
  --footer:#1c1c1c;
  --white:#fff;
}
*{margin:0;padding:0;box-sizing:border-box}
html,body{width:1053px;height:1200px;overflow:hidden;background:var(--white)}
body{position:relative;font-family:Roboto,Arial,sans-serif;color:var(--body)}
.abs{position:absolute}

/* header */
.top-rule{left:0;top:0;width:1053px;height:3px;background:var(--red)}
.header{left:0;top:3px;width:1053px;height:97px;background:linear-gradient(#fafafa,#e2e2e2)}
.header-rule{left:0;top:97px;width:360px;height:3px;background:var(--red)}
.brand{left:176px;top:38px;width:100px;text-align:center}
.brand-mark{display:block;margin:0 auto 6px;width:14px;height:14px;background:var(--red);border-radius:50%}
.brand-name{font:700 15px/1 Roboto,sans-serif;color:var(--red);letter-spacing:1px}
.search{left:714px;top:19px;width:163px;height:28px;background:var(--white);border:1px solid #c9c9c9;border-radius:2px;font:400 9px/26px "Open Sans",sans-serif;color:#444;padding-left:6px}
.search svg{position:absolute;right:9px;top:8px}
.nav{left:348px;top:60px;width:705px;height:40px}
.nav-bg{position:absolute;inset:0}
.nav ul{position:absolute;left:45px;top:0;list-style:none;display:flex;height:40px;align-items:center}
.nav li{font:700 10.5px/1 "Open Sans",sans-serif;color:var(--white);margin-right:36px}

/* hero */
.hero{left:0;top:100px;width:1053px;height:445px;background:linear-gradient(180deg,#8a8a8a 0%,#5b5b5b 45%,#3a3a3a 70%,#6d6d6d 100%)}
.hero-arrow{top:283px}
.caption{background:var(--blue);color:var(--white);font:400 13px/1 Roboto,sans-serif}
.caption-title{left:191px;top:286px;width:347px;height:34px;line-height:34px;padding-left:13px}
.caption-sub{left:176px;top:329px;width:412px;height:34px;line-height:34px;padding-left:28px;font-size:11.5px}
.dots{left:497px;top:520px;display:flex;gap:6px}
.dots span{width:9px;height:9px;border-radius:50%;background:var(--white)}
.dots span.on{background:var(--red);border:1.5px solid var(--white)}

/* sections */
.section-title{font:400 17.5px/1 Roboto,sans-serif;color:var(--red)}
.vision-title{left:175px;top:567px}
.vision-text{left:175px;top:593px;width:415px;font:400 8.3px/16.8px Roboto,sans-serif;color:var(--body)}
.read-more{color:var(--red)}
.services-title{left:619px;top:567px}
.service-list{left:621px;top:596px;width:256px;list-style:none}
.service{display:flex;align-items:center;height:31px;margin-bottom:0.6px;background:var(--grey-row);border-bottom:1px solid var(--grey-line)}
.service-icon{width:38px;height:100%;background:var(--red);display:flex;align-items:center;justify-content:center}
.service-name{flex:1;padding-left:7px;font:400 11.5px/1 Roboto,sans-serif;color:#555}
.service-plus{width:22px;font:700 15px/1 Roboto,sans-serif;color:#222}

/* news */
.news-title{left:175px;top:779px}
.news-nav{left:838px;top:781px;display:flex;gap:3px}
.news-nav span{width:17px;height:18px;background:var(--red);border-radius:2px;display:flex;align-items:center;justify-content:center}
.news-photo{width:145px;height:144px;top:811px}
.photo-a{left:175px;background:linear-gradient(135deg,#2b2b2b,#6b5a4a 55%,#3a3a3a)}
.photo-b{left:535px;background:linear-gradient(160deg,#b7dced,#3f8db5 55%,#0e3c57)}
.news-body{top:811px;width:225px}
.body-a{left:330px}.body-b{left:689px}
.date{position:absolute;left:0;top:0;width:33px;text-align:center}
.date-m{background:var(--red);color:var(--white);font:400 7px/13px Roboto,sans-serif}
.date-d{background:#e4e4e4;color:#222;font:500 10px/20px Roboto,sans-serif}
.meta{position:absolute;left:41px;top:5px;font:400 8px/1 Roboto,sans-serif;color:#111}
.meta-by{position:absolute;left:39px;top:23px;font:400 7.2px/1 Roboto,sans-serif;color:#555}
.meta-by b{font-weight:400;color:var(--red)}
.news-head{position:absolute;left:0;top:46px;font:400 10.4px/17px Roboto,sans-serif;color:var(--red)}
.news-text{position:absolute;left:0;top:78px;width:200px;font:400 8px/12.5px Roboto,sans-serif;color:#444}
.news-more{position:absolute;left:0;top:124px;font:400 8.2px/1 Roboto,sans-serif;color:var(--red)}

/* clients */
.clients-title{left:175px;top:992px}
.client-row{left:190px;top:1030px;width:670px;height:40px;display:flex;justify-content:space-between;align-items:center}
.client{font:500 18px/1 Roboto,sans-serif;color:#555;display:flex;align-items:center;gap:6px}
.client i{width:10px;height:10px;border-radius:50%;background:currentColor;display:block}
.client.c1{color:#2a6cb4}.client.c4{color:#1f4d8f}.client.c5{color:var(--red)}.client.c3{color:#111}

/* footer */
.footer-rule{left:0;top:1115px;width:1053px;height:6px;background:var(--red)}
.footer{left:0;top:1121px;width:1053px;height:79px;background:var(--footer)}
.copyright{left:176px;top:1156px;font:400 10px/1 Roboto,sans-serif;color:var(--white)}
.badge{left:508px;top:1153px;width:67px;height:23px;border-radius:3px;background:#3d7fb8;border:2px solid #aaa}
.social{top:1148px;width:26px;height:26px;border-radius:50%;background:#d8d8d8}
</style>
</head>
<body>
<div class="abs top-rule"></div>
<header class="abs header"></header>
<div class="abs header-rule"></div>
<div class="abs brand"><span class="brand-mark"></span><span class="brand-name">QUELBRANT</span></div>
<div class="abs search">Search...
  <svg width="10" height="10" viewBox="0 0 10 10"><circle cx="4.2" cy="4.2" r="3.2" fill="none" stroke="#333" stroke-width="1.3"/><line x1="6.6" y1="6.6" x2="9.3" y2="9.3" stroke="#333" stroke-width="1.4"/></svg>
</div>
<nav class="abs nav">
  <svg class="nav-bg" width="705" height="40" viewBox="0 0 705 40"><polygon points="46,0 705,0 705,40 0,40" fill="#e8303a"/></svg>
  <ul><li>Home</li><li>Business units</li><li>Services</li><li>About us</li><li>Locations</li><li>Contact Us</li></ul>
</nav>

<div class="abs hero" role="img" aria-label="Photograph of a business team standing behind a close-up handshake"></div>
<svg class="abs hero-arrow" style="left:55px" width="20" height="28" viewBox="0 0 20 28"><polyline points="15,3 5,14 15,25" fill="none" stroke="#fff" stroke-width="5"/></svg>
<svg class="abs hero-arrow" style="left:987px;top:286px" width="20" height="28" viewBox="0 0 20 28"><polyline points="5,3 15,14 5,25" fill="none" stroke="#fff" stroke-width="5"/></svg>
<div class="abs caption caption-title">“Marketing, Sales &amp; Services Enterprise Class Consulting ”</div>
<div class="abs caption caption-sub">Pragmatic Stratagies, Relentless Execution, Insightfull measurements....</div>
<div class="abs dots"><span class="on"></span><span></span><span></span></div>

<h2 class="abs section-title vision-title">Quelbrant Our Vision</h2>
<p class="abs vision-text">quelbrant specializes in delivering quality professional services and technical projects that support larger business goals.&nbsp; systems are tools that support a greater business function and need. we understand that most technical projects are conceptualized to support a larger vision with actual business goals in mind and ensure that all of our professional and certified expertise is included in our professional services to meet those goals.<br>quelbrant recognizes the middle east and greater asia regions are economic growth markets with developing infrastructure projects requiring specialist systems and technical expertise.&nbsp; accordingly, quelbrant has evolved its presence in the regions to meet client demands and expectations.<br><span class="read-more">Read more +</span></p>

<h2 class="abs section-title services-title">Services</h2>
<ul class="abs service-list">
  <li class="service"><span class="service-icon"><svg width="16" height="18" viewBox="0 0 16 18" fill="none" stroke="#fff" stroke-width="1.6"><path d="M3 2h10M5 2v6h6V2M8 8v8M4 16h8M5 11h6"/></svg></span><span class="service-name">Consulting</span><span class="service-plus">+</span></li>
  <li class="service"><span class="service-icon"><svg width="18" height="18" viewBox="0 0 18 18"><circle cx="9" cy="9" r="5" fill="none" stroke="#fff" stroke-width="2.4" stroke-dasharray="2.6 1.3"/><circle cx="9" cy="9" r="2" fill="none" stroke="#fff" stroke-width="1.5"/></svg></span><span class="service-name">Engineering</span><span class="service-plus">+</span></li>
  <li class="service"><span class="service-icon"><svg width="20" height="18" viewBox="0 0 20 18"><polygon points="10,2 18,16 2,16" fill="none" stroke="#fff" stroke-width="2" stroke-linejoin="round"/><rect x="9.1" y="7" width="1.8" height="5" fill="#fff"/><rect x="9.1" y="13" width="1.8" height="1.8" fill="#fff"/></svg></span><span class="service-name">Construction</span><span class="service-plus">+</span></li>
  <li class="service"><span class="service-icon"><svg width="20" height="18" viewBox="0 0 20 18" fill="none" stroke="#fff" stroke-width="1.6"><circle cx="10" cy="9" r="2.5"/><circle cx="10" cy="9" r="5.5"/><path d="M2 5a9 9 0 0 0 0 8M18 5a9 9 0 0 1 0 8"/></svg></span><span class="service-name">Operations</span><span class="service-plus">+</span></li>
  <li class="service"><span class="service-icon"><svg width="18" height="18" viewBox="0 0 18 18" stroke="#fff" stroke-width="2.2" stroke-linecap="round"><line x1="3" y1="3" x2="15" y2="15"/><line x1="15" y1="3" x2="3" y2="15"/></svg></span><span class="service-name">Maintenance</span><span class="service-plus">+</span></li>
</ul>

<h2 class="abs section-title news-title">News / Events</h2>
<div class="abs news-nav">
  <span><svg width="6" height="9" viewBox="0 0 6 9"><polyline points="5,1 1,4.5 5,8" fill="none" stroke="#fff" stroke-width="1.5"/></svg></span>
  <span><svg width="6" height="9" viewBox="0 0 6 9"><polyline points="1,1 5,4.5 1,8" fill="none" stroke="#fff" stroke-width="1.5"/></svg></span>
</div>

<div class="abs news-photo photo-a" role="img" aria-label="Photograph of a smiling businessman with colleagues behind"></div>
<article class="abs news-body body-a">
  <div class="date"><div class="date-m">Aug</div><div class="date-d">01</div></div>
  <div class="meta">Morlenda Studio</div>
  <div class="meta-by">Posted By <b>Tavin Orrell</b></div>
  <h3 class="news-head" style="font-weight:400">Lorem ipsum dolor sit amet, consectetur<br>adipiscing elit</h3>
  <p class="news-text">lorem ipsum dolor sit amet, consectetur adipiscing elit. Proin venenatis aliquam diam, nec volutpat dolor consequat et.</p>
  <span class="news-more">Read More +</span>
</article>

<div class="abs news-photo photo-b" role="img" aria-label="Illustration of a person surrounded by floating digital screens"></div>
<article class="abs news-body body-b">
  <div class="date"><div class="date-m">Aug</div><div class="date-d">01</div></div>
  <div class="meta">Morlenda Studio</div>
  <div class="meta-by">Posted By <b>Tavin Orrell</b></div>
  <h3 class="news-head" style="font-weight:400">Lorem ipsum dolor sit amet, consectetur<br>adipiscing elit</h3>
  <p class="news-text">lorem ipsum dolor sit amet, consectetur adipiscing elit. Proin venenatis aliquam diam, nec volutpat dolor consequat et.</p>
  <span class="news-more">Read More +</span>
</article>

<h2 class="abs section-title clients-title">Clients</h2>
<div class="abs client-row">
  <span class="client c1"><i></i>Brevanta</span>
  <span class="client c2">Cloudmera</span>
  <span class="client c3">Ostrel</span>
  <span class="client c4"><i></i>Vantuo</span>
  <span class="client c5">Quarrix</span>
</div>

<div class="abs footer-rule"></div>
<footer class="abs footer"></footer>
<div class="abs copyright">Copyright 2005-2013 www.quelbrant-example.biz All rights reserved.</div>
<div class="abs badge" role="img" aria-label="Hosting partner badge"></div>
<span class="abs social" style="left:784px" aria-label="Chatterloop"></span>
<span class="abs social" style="left:816px" aria-label="Social network"></span>
<span class="abs social" style="left:847px" aria-label="Professional network"></span>
</body>
</html>
```